Website Redesign Brief for Breezeline Climate Services WA

Creating a clear and concise brief for designers to redesign your website, https://breezelineclimatewa.com.au/, is essential to ensure the project aligns with your vision for a more energetic, friendly, optimistic, and user-friendly website. Below is a sample brief tailored to your request, balancing specificity with flexibility to allow designers to bring their creativity to the table.

Website Redesign Brief for Breezeline Climate WA
1. Project Overview

We are seeking a redesign of our website, https://breezelineclimatewa.com.au/, to create a vibrant, engaging, and user-friendly online presence that reflects our brand’s commitment to providing top-notch air conditioning services in Western Australia. The redesigned website should feel energetic, friendly, and optimistic while maintaining professionalism and improving user experience.
2. Goals and Objectives

Enhance Brand Perception: Convey a modern, approachable, and positive brand identity that resonates with both residential and commercial clients.
Improve User Experience: Simplify navigation, improve accessibility, and ensure a seamless experience across devices (desktop, tablet, mobile).
Increase Engagement: Encourage visitors to explore services, request quotes, and contact us through clear calls-to-action (CTAs).
Boost Conversion Rates: Make it easier for users to find information and take action (e.g., booking services or inquiries).
Showcase Expertise: Highlight our professional air conditioning services, experience, and customer satisfaction in an inviting way.

3. Target Audience

Primary Audience: Homeowners and small business owners in Western Australia seeking air conditioning installation, maintenance, or repair services.
Secondary Audience: Property managers, commercial clients, and real estate professionals looking for reliable HVAC solutions.
Demographics: Ages 25–65, mix of tech-savvy and non-tech-savvy users, located primarily in Perth and surrounding areas.
User Needs: Clear information about services, transparent pricing, easy contact options, and reassurance of quality and reliability.

4. Design Preferences

Tone and Style:

Energetic: Use bold, vibrant colors (e.g., blues, whites, and pops of warm tones like orange or yellow) to evoke energy and optimism.
Friendly: Incorporate approachable language, welcoming imagery, and a clean, uncluttered layout.
Optimistic: Highlight positive customer outcomes (e.g., comfort, energy savings) through visuals and messaging.
Professional yet approachable: Maintain credibility as a trusted service provider while avoiding a cold or overly corporate feel.

Visual Elements:

Use high-quality images of happy customers, comfortable homes/offices, and modern air conditioning units.
Incorporate subtle animations or micro-interactions to add energy (e.g., hover effects on buttons or smooth scrolling).
Avoid overly complex graphics that may slow down the site or distract from usability.

Typography: Clean, modern fonts that are easy to read. Use larger, bold headings for hierarchy and warmth.
Inspiration: Websites like https://www.vorlex.com.au/ (clean and professional) or https://www.tandoraclimatech.com.au/ (user-friendly and modern) but with a more vibrant and welcoming vibe.

5. Functional Requirements

User-Friendly Navigation: Simplify the menu structure to make key pages (e.g., Services, About Us, Contact) easily accessible.
Mobile Responsiveness: Ensure the site is fully optimized for mobile devices, with fast load times and intuitive touch interactions.
Key Features:

Prominent CTAs for requesting quotes, booking services, or contacting the team.
A clear service overview with icons or visuals for each service (e.g., installation, repairs, maintenance).
A testimonials section to showcase customer satisfaction.
An easy-to-use contact form with minimal fields.
Integration with Google Maps for location-based services or office directions.

SEO and Performance: Optimize for search engines (e.g., keywords like “air conditioning Perth”) and ensure fast loading speeds.
Accessibility: Follow WCAG guidelines to ensure the site is usable for all visitors, including those with disabilities.

6. Content Guidance

Existing Content: Review and refine current content from https://breezelineclimatewa.com.au/ to make it concise, engaging, and aligned with the friendly tone.
New Content Ideas:

Add a “Why Choose Us” section highlighting expertise, customer service, and eco-friendly solutions.
Include a FAQ page to address common customer questions.
Create a blog section for tips on air conditioning maintenance or energy efficiency (optional).

Tone of Voice: Conversational, reassuring, and positive. Avoid technical jargon unless clearly explained.

7. Technical Considerations

Platform: Open to recommendations (e.g., WordPress, Wix, or custom-built) but prioritize ease of maintenance and scalability.
Integrations: Ensure compatibility with existing tools (e.g., Google Analytics, CRM for quote requests, or booking systems).
Domain and Hosting: Retain current domain (breezelineclimatewa.com.au); hosting recommendations welcome.
Timeline: Initial design concepts within [insert timeline, e.g., 2–3 weeks], with full redesign completed by [insert deadline, e.g., 6–8 weeks].
Budget: [Insert budget range or state “flexible, please provide a quote”].

8. Deliverables

Wireframes and mockups for homepage, service pages, and contact page.
Fully responsive website design with all necessary pages.
Style guide (colors, fonts, imagery guidelines).
CMS setup (if applicable) with basic training for content updates.
Testing and optimization for performance and SEO.

9. Success Metrics

Increased time on site and reduced bounce rate.
Higher conversion rates for quote requests and contact form submissions.
Positive user feedback on ease of navigation and overall experience.
Improved search engine rankings for key terms within [insert timeframe, e.g., 3 months].

10. Additional Notes

Please provide a portfolio of similar projects or examples of user-friendly, vibrant websites.
We are open to creative suggestions to make the website stand out in the HVAC industry.
Regular progress updates and collaboration during the design process are appreciated.
Updates

designers are asking for more time

few have requested an extension. I Have extended

Target Market(s)

Primary Audience: Homeowners and small business owners in Western Australia seeking air conditioning installation, maintenance, or repair services. Secondary Audience: Property managers, commercial clients, and real estate professionals looking for reliable HVAC solutions. Demographics: Ages 25–65, mix of tech-savvy and non-tech-savvy users, located primarily in Perth and surrounding areas. User Needs: Clear information about services, transparent pricing, easy contact options, and reassurance of quality and reliability.

Industry/Entity Type

Air Conditioning and Refrigeration (HVAC & R)

Coding

Coded - Design and coding required

Colors
0054AA
0677BA
7BADD7
CADEEF
E8F1F8
59FF00
82FF00
B8FF75
E3FFCB
F4FFEA
F0912C
F2A743
F7CA91
FBE8D2
FDF5EE
EE7325
F08F49
F5BC92
FAE3D3
FDF4ED

Requirements
Must have
• Must have all my current information I currently have on my web page.
Nice to have
• A sales page for people to buy products online

```html
<!DOCTYPE html>
<html lang="en">
<head>
<meta charset="utf-8">
<title>About – Quellair WA</title>
<link href="https://fonts.googleapis.com/css2?family=Poppins:wght@500;600&family=Inter:wght@400;500;700&display=swap" rel="stylesheet">
<style>
:root{
  --ink:#141414;
  --dark:#140c08;
  --orange:#f26a1b;
  --peach:#fdeee2;
  --sky:#e8f0f7;
  --line:#2a2a2a;
  --muted:#3a3a3a;
  --white:#ffffff;
}
*{box-sizing:border-box;margin:0;padding:0}
html,body{width:1200px;height:2382px;overflow:hidden}
body{font-family:"Inter",sans-serif;color:var(--ink);background:var(--white);position:relative}
h1,h2,h3{font-family:"Poppins",sans-serif;font-weight:600}
a{color:inherit;text-decoration:none}

.site-header{position:absolute;top:0;left:0;width:1200px;height:121px;background:var(--white)}
.brand{position:absolute;left:100px;top:36px;display:flex;align-items:center;gap:14px}
.brand-dot{width:44px;height:44px;border-radius:50%;background:var(--orange)}
.brand-name{font-family:"Poppins",sans-serif;font-weight:600;font-size:23px;color:var(--ink)}
.main-nav{position:absolute;left:583px;top:49px;display:flex;gap:31px;font-size:14px}
.main-nav .active,.footer-nav .active{color:var(--orange)}
.btn-outline{position:absolute;left:944px;top:38px;width:161px;height:39px;border:2px solid var(--ink);border-radius:20px;display:flex;align-items:center;justify-content:center;font-size:12px;font-weight:700}

.hero{position:absolute;top:121px;left:0;width:1200px;height:348px;background:var(--dark);overflow:hidden}
.hero-media{position:absolute;left:640px;top:0;width:560px;height:348px;background:linear-gradient(135deg,#3a3d44 0%,#1f2a3a 45%,#2b3442 70%,#6a5a2a 100%)}
.hero-title{position:absolute;left:214px;top:124px;color:var(--white);font-size:42px;line-height:49px}

.partner{position:absolute;top:469px;left:0;width:1200px;height:506px;background:var(--peach)}
.partner h2{position:absolute;left:100px;top:85px;font-size:30px}
.partner-photo{position:absolute;left:100px;top:172px;width:469px;height:334px;border-top-right-radius:125px;background:linear-gradient(160deg,#8a7a66 0%,#c9a57a 40%,#e6d6bd 70%,#2a2420 100%)}
.partner-copy{position:absolute;left:636px;top:173px;width:470px;font-size:14px;line-height:23px;color:var(--muted)}
.partner-copy p+p{margin-top:16px}

.journey{position:absolute;top:975px;left:0;width:1200px;height:498px;background:var(--sky)}
.journey h2{position:absolute;left:100px;top:83px;width:340px;font-size:30px;line-height:37px}
.journey-intro{position:absolute;left:100px;top:219px;width:360px;font-size:14px;line-height:23px;color:var(--muted)}
.stat{position:absolute;left:520px;width:585px}
.stat-num{position:absolute;left:0;top:0;font-family:"Poppins",sans-serif;font-weight:500;font-size:40px;color:var(--orange);line-height:44px}
.stat-label{position:absolute;left:0;top:52px;font-size:14px}
.stat-text{position:absolute;left:171px;top:8px;width:414px;font-size:14px;line-height:23px;color:var(--muted)}
.stat-rule{position:absolute;left:520px;width:585px;height:1px;background:var(--line)}

.experts{position:absolute;top:1473px;left:0;width:1200px;height:460px;background:var(--peach);text-align:center}
.experts h2{position:absolute;left:0;top:83px;width:1200px;font-size:30px}
.experts-sub{position:absolute;left:0;top:140px;width:1200px;font-size:14px;color:var(--muted)}
.expert{position:absolute;top:210px;width:250px}
.expert-photo{width:83px;height:83px;border-radius:50%;margin:0 auto;background:linear-gradient(160deg,#b58a6a,#5a4232)}
.expert h3{margin-top:16px;font-size:24px;font-weight:600}
.expert p{margin-top:10px;font-size:14px;color:var(--muted)}

.cta{position:absolute;top:1933px;left:0;width:1200px;height:382px;background:linear-gradient(120deg,#2a1c14 0%,#1a110c 50%,#3a2a20 100%);text-align:center;color:var(--white)}
.cta h2{position:absolute;left:310px;top:92px;width:580px;font-size:30px;line-height:38px}
.cta-text{position:absolute;left:310px;top:178px;width:580px;font-size:14px;line-height:23px}
.btn-solid{position:absolute;left:513px;top:254px;width:179px;height:44px;border-radius:22px;background:var(--orange);display:flex;align-items:center;justify-content:center;font-size:13px;font-weight:700;color:var(--white)}

.site-footer{position:absolute;top:2315px;left:0;width:1200px;height:67px;background:var(--white)}
.footer-nav{position:absolute;left:100px;top:24px;display:flex;gap:14px;font-size:14px}
.copyright{position:absolute;right:95px;top:24px;font-size:14px}
</style>
</head>
<body>

<header class="site-header">
  <a class="brand" href="#"><span class="brand-dot"></span><span class="brand-name">Quellair WA</span></a>
  <nav class="main-nav">
    <a href="#">Home</a><a class="active" href="#">About</a><a href="#">Services</a><a href="#">Blog</a><a href="#">Contact</a>
  </nav>
  <a class="btn-outline" href="#">REQUEST A QUOTE</a>
</header>

<section class="hero">
  <div class="hero-media" role="img" aria-label="Close-up of an air conditioning control panel with gauges and buttons"></div>
  <svg width="1200" height="348" style="position:absolute;left:0;top:0">
    <path d="M0 0 H880 C880 220 800 335 650 348 H0 Z" fill="#140c08"/>
  </svg>
  <h1 class="hero-title">Discover The Heart<br>Of Quellair WA</h1>
</section>

<section class="partner">
  <h2>Your Trusted Partner For Climate Solutions In Perth</h2>
  <div class="partner-photo" role="img" aria-label="Modern office lounge with a ceiling cassette air conditioner"></div>
  <div class="partner-copy">
    <p>At Quellair WA, we’ve transformed countless homes and businesses, ensuring our clients enjoy the comfort of efficient, reliable air conditioning systems tailored to their needs.</p>
    <p>Our commitment to excellence and customer satisfaction has made us a preferred choice in the Perth area.</p>
  </div>
</section>

<section class="journey">
  <h2>Our Journey Through Innovation And Service</h2>
  <p class="journey-intro">Founded to provide exceptional air conditioning services, Quellair WA has built a solid reputation through dedication to quality, efficiency, and customer care over the years.</p>

  <div class="stat" style="top:87px">
    <div class="stat-num">0+</div>
    <div class="stat-label">Experience</div>
    <p class="stat-text">With over 15 years of experience, Quellair WA delivers expertise and reliability in every project we undertake.</p>
  </div>
  <div class="stat-rule" style="top:180px"></div>

  <div class="stat" style="top:217px">
    <div class="stat-num">0+</div>
    <div class="stat-label">Happy Clients</div>
    <p class="stat-text">Our team comprises over 20 skilled technicians, ensuring prompt and professional service on every job.</p>
  </div>
  <div class="stat-rule" style="top:309px"></div>

  <div class="stat" style="top:347px">
    <div class="stat-num">0</div>
    <div class="stat-label" style="top:54px">Employees</div>
    <p class="stat-text">We have proudly served thousands of satisfied clients across Perth and Western Australia, continually exceeding their expectations.</p>
  </div>
</section>

<section class="experts">
  <h2>Meet Our Experts</h2>
  <p class="experts-sub">Dedicated professionals committed to delivering outstanding air conditioning solutions for you.</p>
  <div class="expert" style="left:101px">
    <div class="expert-photo" role="img" aria-label="Portrait of team member" style="background:linear-gradient(160deg,#d9a56a,#e0b82a)"></div>
    <h3>Marcus Delaney</h3><p>Designer</p>
  </div>
  <div class="expert" style="left:352px">
    <div class="expert-photo" role="img" aria-label="Portrait of team member" style="background:linear-gradient(160deg,#e8eef2,#9aa8b4)"></div>
    <h3>Owen Castell</h3><p>Dancer</p>
  </div>
  <div class="expert" style="left:603px">
    <div class="expert-photo" role="img" aria-label="Portrait of team member" style="background:linear-gradient(160deg,#6a5a4a,#2a2420)"></div>
    <h3>Tobias Renfield</h3><p>Business Admin</p>
  </div>
  <div class="expert" style="left:854px">
    <div class="expert-photo" role="img" aria-label="Portrait of team member" style="background:linear-gradient(160deg,#7a2a2a,#2f4a2a)"></div>
    <h3>Liam Harrow</h3><p>Painter</p>
  </div>
</section>

<section class="cta" role="img" aria-label="Dimmed photo of a technician servicing an outdoor air conditioning unit">
  <h2>Contact Us For Quality Air Solutions Now!</h2>
  <p class="cta-text">Quellair WA is your go-to partner for all air conditioning needs. We provide quality services that ensure comfort and satisfaction for every client.</p>
  <a class="btn-solid" href="#">REQUEST A QUOTE</a>
</section>

<footer class="site-footer">
  <nav class="footer-nav">
    <a href="#">Home</a><a class="active" href="#">About</a><a href="#">Services</a><a href="#">Blog</a><a href="#">Contact</a>
  </nav>
  <p class="copyright">Copyright © 2025 Quellair WA</p>
</footer>

</body>
</html>
```